Suds & Woofs 2nd Annual Fundraiser

I am a Realtor sponsoring the 2nd annual fundraiser on behalf of Allies of Cedar Hollow Animal Haven. Like the flyer to be professional yet fun and inviting. Please see the attached file below. The 1st annual flyer was fun but not as professional, modern or inviting as I would have liked it to be.
Target Market(s)
Dog lovers in Ponte Vedra, Ponte Vedra Beach and Nocatee Florida
Logo Text
Needed
Font styles to use
Other font styles liked:
- Font that fits the style of the fundraiser
Colors
886aae
abd036
Requirements
Must have
- Please see the attached flyer and photos.
- This will be the 2nd Annual on Saturday, April 27, 2019 from 10AM - 1PM. Same location: Pemberly Realty, 418 Harrowgate Ln. Ponte Vedra FL 32940

```html
<!DOCTYPE html>
<html lang="en">
<head>
<meta charset="utf-8">
<title>Suds &amp; Woofs Doggie Wash Extravaganza</title>
<link rel="stylesheet" href="https://fonts.googleapis.com/css2?family=Montserrat:wght@500;700;800;900&family=Open+Sans:wght@400;600;700&display=swap">
<style>
  :root {
    --purple: #6f3d8f;
    --purple-soft: #886aae;
    --green: #abd036;
    --green-deep: #8cb322;
    --ink: #4a2a63;
    --text: #333;
    --white: #fff;
  }
  * { margin: 0; padding: 0; box-sizing: border-box; }
  html, body { width: 847px; height: 1200px; overflow: hidden; background: var(--white); }
  .flyer { position: relative; width: 847px; height: 1200px; overflow: hidden; font-family: "Open Sans", sans-serif; color: var(--text); }
  .hero { position: absolute; left: 0; top: 0; width: 847px; height: 700px; }

  .support { position: absolute; right: 28px; top: 22px; width: 260px; text-align: center; }
  .support-label { font-family: "Montserrat", sans-serif; font-weight: 600; font-size: 20px; color: var(--ink); margin-bottom: 10px; }
  .org-name { display: flex; align-items: center; justify-content: center; gap: 10px; }
  .org-dot { width: 26px; height: 26px; border-radius: 50%; background: var(--purple-soft); flex: none; }
  .org-text { font-family: "Montserrat", sans-serif; font-weight: 800; font-size: 17px; line-height: 1.15; color: var(--purple); text-align: left; }
  .org-tagline { font-size: 11px; color: var(--ink); margin-top: 6px; font-style: normal; }

  .headline { position: absolute; left: 40px; top: 672px; font-family: "Montserrat", sans-serif; }
  .headline .edition { font-weight: 800; font-size: 40px; color: var(--purple); letter-spacing: 0.5px; line-height: 1; }
  .headline .title { font-weight: 900; font-size: 62px; color: var(--purple); line-height: 1.05; margin-top: 6px; }
  .headline .subtitle { font-weight: 800; font-size: 36px; color: var(--green-deep); line-height: 1.1; }

  .tagline-band { position: absolute; left: 0; top: 842px; width: 440px; height: 38px; background: var(--green); border-radius: 0 19px 19px 0; display: flex; align-items: center; padding-left: 40px; }
  .tagline-band span { font-family: "Montserrat", sans-serif; font-weight: 700; font-size: 21px; color: var(--white); }

  .features { position: absolute; left: 40px; top: 895px; display: grid; grid-template-columns: 270px 250px; row-gap: 4px; list-style: none; }
  .features li { font-family: "Montserrat", sans-serif; font-weight: 700; font-size: 18px; color: var(--ink); display: flex; align-items: center; gap: 10px; }
  .features li::before { content: ""; width: 13px; height: 13px; background: var(--purple-soft); flex: none; }

  .donate { position: absolute; left: 110px; top: 988px; width: 480px; text-align: center; font-size: 15px; color: var(--text); line-height: 1.3; }
  .note { position: absolute; left: 40px; top: 1038px; width: 570px; font-weight: 700; font-size: 15px; line-height: 1.35; color: var(--purple); }

  .contacts { position: absolute; left: 60px; top: 1090px; width: 520px; display: flex; justify-content: space-between; font-size: 10.5px; line-height: 1.35; text-align: center; color: var(--text); }
  .contact strong { font-weight: 700; }

  .mascot { position: absolute; right: 0; top: 880px; width: 236px; height: 270px; background: radial-gradient(ellipse at 50% 40%, #c08a55 0%, #9b6a3f 55%, #e8ddd0 100%); border-radius: 110px 110px 0 0; }

  .date-bar { position: absolute; left: 0; bottom: 0; width: 847px; height: 58px; background: var(--purple); display: flex; align-items: center; color: var(--white); font-family: "Montserrat", sans-serif; font-weight: 700; font-size: 17px; }
  .date-bar::before { content: ""; position: absolute; left: 0; top: -8px; width: 847px; height: 8px; background: var(--green); }
  .date-bar .when { padding-left: 28px; width: 270px; line-height: 1.2; }
  .date-bar .where { line-height: 1.2; }
</style>
</head>
<body>
<main class="flyer">
  <svg class="hero" viewBox="0 0 847 700" xmlns="http://www.w3.org/2000/svg">
    <defs>
      <linearGradient id="photoTones" x1="0" y1="0" x2="1" y2="1">
        <stop offset="0" stop-color="#6f7a62"/>
        <stop offset="0.45" stop-color="#8b8478"/>
        <stop offset="1" stop-color="#b3ada3"/>
      </linearGradient>
    </defs>
    <path role="img" aria-label="Photo of volunteers washing a dog with soapy water outdoors" d="M0,0 H847 V540 Q520,575 0,668 Z" fill="url(#photoTones)"/>
    <path class="corner-band" d="M520,0 Q540,170 660,232 Q760,270 847,252 V0 Z" fill="var(--green)"/>
    <path class="corner-band" d="M534,0 Q556,158 668,216 Q762,252 847,236 V0 Z" fill="var(--purple-soft)"/>
    <path class="corner-panel" d="M548,0 Q570,146 676,202 Q764,236 847,220 V0 Z" fill="var(--white)"/>
    <path class="wave-band" d="M0,640 Q500,540 847,520 V560 Q520,585 0,690 Z" fill="var(--green)"/>
    <path class="wave-band" d="M0,668 Q520,575 847,555 V600 Q540,610 0,700 Z" fill="var(--purple-soft)"/>
  </svg>

  <aside class="support">
    <p class="support-label">In Support of</p>
    <div class="org-name">
      <span class="org-dot"></span>
      <span class="org-text">Allies of Cedar Hollow<br>Animal Haven</span>
    </div>
    <p class="org-tagline">Adopt a forever friend</p>
  </aside>

  <header class="headline">
    <p class="edition">SECOND ANNUAL</p>
    <h1 class="title">SUDS &amp; WOOFS</h1>
    <p class="subtitle">DOGGIE WASH EXTRAVAGANZA</p>
  </header>

  <div class="tagline-band"><span>A Family Fun Event for All Ages</span></div>

  <ul class="features">
    <li>FREE doggy Wash</li>
    <li>Raffle Drawing</li>
    <li>Food &amp; Beverages</li>
    <li>Grand Prize</li>
    <li>Vendors (FREE give-a-ways)</li>
    <li>Donations Welcome</li>
  </ul>

  <p class="donate">To make a donation: https://www.example.org/achah<br>Click: DONATE</p>

  <p class="note">All domestic breeds from puppies to seniors invited. Please be sure Furry Fido is tolerant of other dogs, crowds and bathing.</p>

  <section class="contacts">
    <div class="contact"><strong>Marlena Voss</strong><br>Pemberly Realty Corp.<br>904.555.0142<br>marlenavoss@pemberlyrealty.com</div>
    <div class="contact"><strong>Dana Whitfield</strong><br>ACHAH<br>904.555.0187<br>dana.whitfield@mailbox.net</div>
  </section>

  <div class="mascot" role="img" aria-label="Costumed dog mascot character giving a thumbs up"></div>

  <footer class="date-bar">
    <div class="when">Saturday, April 27th<br>10 AM - 1 PM</div>
    <div class="where">Location: Pemberly Realty, 418 Harrowgate Ln.<br>Ponte Vedra FL 32940</div>
  </footer>
</main>
</body>
</html>
```